Velmarotix - world unique technology for better life - please let them know who am i at first sight

We need a new business card for company which is a provider of unique crystal based technology suitable for all living being. For more information and final design you can use our brochure (our colours are black and blue from brochure).
We use Verdana font

Industry/Entity Type

Business

Contact Information for Business Card

regular dimension

Font styles to use
Other font styles liked:
• Verdana

Requirements
Must have
• Logo
• name
• function/position
• phone
• mobile
• e-mail
• adress
Nice to have
• inovative design (technology directed)

```html
<!DOCTYPE html>
<html lang="en">
<head>
<meta charset="utf-8">
<title>Velmarotix business cards</title>
<link rel="stylesheet" href="https://fonts.googleapis.com/css2?family=Noto+Sans:wght@400;700&display=swap">
<style>
  :root {
    --backdrop: #d8c79c;
    --card-black: #0b0b0c;
    --brand-blue: #1fa3e0;
    --light-blue: #2fb2ee;
    --silver: #b9bcc0;
    --white: #ffffff;
    --font-main: Verdana, "Noto Sans", sans-serif;
  }
  * { box-sizing: border-box; margin: 0; padding: 0; }
  html, body {
    width: 1200px; height: 978px; overflow: hidden;
    background: var(--backdrop);
    font-family: var(--font-main);
  }
  .canvas { position: relative; width: 1200px; height: 978px; }
  .card {
    position: absolute; left: 220px; width: 760px; height: 434px;
    border-radius: 34px; background: var(--card-black); overflow: hidden;
  }
  .card--back { top: 40px; }
  .card--front { top: 504px; }

  .brand {
    display: flex; align-items: center; gap: 18px;
    color: var(--brand-blue); font-size: 50px; font-weight: 400;
    letter-spacing: 1px; line-height: 1;
  }
  .brand__dot {
    width: 58px; height: 58px; border-radius: 50%;
    background: var(--brand-blue); flex: none;
  }
  .card--back .brand { position: absolute; left: 0; right: 0; top: 150px; justify-content: center; }
  .card--back .website {
    position: absolute; left: 0; right: 0; top: 262px; text-align: center;
    color: var(--white); font-size: 22px; font-weight: 700; letter-spacing: 2px;
  }

  .card--front .swoosh { position: absolute; inset: 0; }
  .card--front .brand { position: absolute; left: 250px; top: 44px; font-size: 40px; }
  .card--front .brand__dot { width: 46px; height: 46px; }
  .person { position: absolute; left: 46px; top: 128px; }
  .person__name { color: var(--light-blue); font-size: 26px; font-weight: 700; }
  .person__role { color: var(--white); font-size: 16px; margin-top: 6px; }

  .contacts {
    position: absolute; right: 44px; top: 322px; list-style: none;
    color: var(--white); font-size: 17px; line-height: 25px;
  }
  .contacts li { display: flex; align-items: center; justify-content: flex-end; gap: 10px; }
  .contacts svg { width: 16px; height: 16px; flex: none; }
  .address {
    position: absolute; left: 46px; bottom: 24px;
    color: var(--white); font-size: 16px;
  }
</style>
</head>
<body>
<main class="canvas">
  <section class="card card--back" aria-label="Card back">
    <div class="brand"><span class="brand__dot"></span>VELMAROTIX</div>
    <p class="website">www.velmarotix.cu</p>
  </section>

  <section class="card card--front" aria-label="Card front">
    <svg class="swoosh" viewBox="0 0 760 434" aria-hidden="true">
      <path d="M0 195 C230 235 460 350 760 300 L760 318 C460 368 230 258 0 224 Z" fill="var(--silver)"/>
      <path d="M0 224 C230 258 460 368 760 318 L760 434 L0 434 Z" fill="var(--brand-blue)"/>
    </svg>
    <div class="brand"><span class="brand__dot"></span>VELMAROTIX</div>
    <div class="person">
      <p class="person__name">Lorena Dravik</p>
      <p class="person__role">Founder and CEO</p>
    </div>
    <ul class="contacts">
      <li>
        <svg viewBox="0 0 16 16" aria-hidden="true"><path d="M4 1 L6.5 4.5 L5 6.5 C6 8.5 7.5 10 9.5 11 L11.5 9.5 L15 12 L13 15 C7 14 2 9 1 3 Z" fill="var(--white)"/></svg>
        012-345-6789
      </li>
      <li>
        <svg viewBox="0 0 16 16" aria-hidden="true"><rect x="4" y="1" width="8" height="14" rx="1.5" fill="var(--white)"/><rect x="5.5" y="3" width="5" height="8" fill="var(--brand-blue)"/></svg>
        012-345-6789
      </li>
      <li>
        <svg viewBox="0 0 16 16" aria-hidden="true"><rect x="1" y="3" width="14" height="10" rx="1" fill="var(--white)"/><path d="M1.5 3.5 L8 9 L14.5 3.5" stroke="var(--brand-blue)" stroke-width="1.4" fill="none"/></svg>
        info@velmarotix.cu
      </li>
      <li>
        <svg viewBox="0 0 16 16" aria-hidden="true"><circle cx="8" cy="8" r="6.5" stroke="var(--white)" stroke-width="1.5" fill="none"/><path d="M1.5 8 H14.5 M8 1.5 C5 5 5 11 8 14.5 M8 1.5 C11 5 11 11 8 14.5" stroke="var(--white)" stroke-width="1.2" fill="none"/></svg>
        www.velmarotix.cu
      </li>
    </ul>
    <p class="address">Street Name, City Name, Zipcode-01234</p>
  </section>
</main>
</body>
</html>
```